Business Card - Tidal Lanes

Need Business Card design for company named Tidal Lanes. Software development focused mainly on Brindle Orvix & Zelt Apps. I've attached our logo with both a black and white background. Please add trademark symbol to logo when using.

```html
<!DOCTYPE html>
<html lang="en">
<head>
<meta charset="utf-8">
<title>Tidal Lanes – Business Card</title>
<link rel="stylesheet" href="https://fonts.googleapis.com/css2?family=Source+Sans+3:wght@400;600;700&display=swap">
<style>
  :root {
    --backdrop: #ece8e3;
    --ink-black: #0d0d0d;
    --brand-red: #d71a1f;
    --band-yellow: #ffc20f;
    --band-orange: #f79a1c;
    --accent-yellow: #f6b316;
    --paper-white: #ffffff;
    --soft-white: #e9e9e9;
    --divider: #8a8a8a;
  }
  * { box-sizing: border-box; margin: 0; padding: 0; }
  html, body {
    width: 1200px; height: 720px; overflow: hidden;
    background: var(--backdrop);
    font-family: "Source Sans 3", "Myriad Pro", sans-serif;
  }
  .canvas { position: relative; width: 1200px; height: 720px; }

  .card {
    position: absolute; top: 212px;
    width: 520px; height: 297px;
    border-radius: 4px; overflow: hidden;
    box-shadow: 0 6px 18px rgba(0,0,0,.18);
  }

  /* Front side */
  .card--front { left: 50px; background: var(--ink-black); }
  .front__band {
    position: absolute; left: 0; top: 0; width: 100%; height: 98px;
    background: linear-gradient(to bottom, var(--band-yellow) 0%, var(--band-yellow) 45%, var(--band-orange) 100%);
  }
  .front__rule {
    position: absolute; left: 0; top: 98px; width: 100%; height: 3px;
    background: var(--brand-red);
  }
  .front__brand {
    position: absolute; left: 0; top: 118px; width: 100%;
    text-align: center; color: var(--paper-white);
    font-weight: 700; font-size: 30px; letter-spacing: -0.3px;
  }
  .front__details {
    position: absolute; left: 0; top: 178px; width: 100%;
    display: flex; justify-content: center; align-items: flex-start;
  }
  .person {
    width: 200px; text-align: right; padding-right: 16px;
    color: var(--soft-white); font-size: 14px; line-height: 1.2;
  }
  .person__name { color: var(--accent-yellow); font-weight: 700; font-size: 19px; }
  .person__title { margin-bottom: 10px; }
  .details__divider { width: 1px; height: 76px; background: var(--divider); }
  .contact {
    width: 200px; padding-left: 16px;
    color: var(--soft-white); font-size: 15px; line-height: 1.5;
  }
  .contact__line { display: flex; align-items: center; gap: 8px; }
  .contact__icon { width: 13px; height: 15px; flex: none; }

  /* Back side */
  .card--back { left: 630px; background: var(--brand-red); }
  .back__brand {
    position: absolute; left: 0; top: 96px; width: 100%;
    text-align: center; color: var(--paper-white);
    font-weight: 700; font-size: 58px; letter-spacing: -0.5px;
  }
  .back__web {
    position: absolute; left: 0; bottom: 30px; width: 100%;
    text-align: center; color: var(--paper-white);
    font-size: 15px; letter-spacing: 0.6px;
  }
</style>
</head>
<body>
<main class="canvas">

  <section class="card card--front" aria-label="Card front">
    <div class="front__band"></div>
    <div class="front__rule"></div>
    <div class="front__brand">Tidal Lanes™</div>

    <div class="front__details">
      <div class="person">
        <div class="person__name">Your Name</div>
        <div class="person__title">Title</div>
        <div class="person__address">4120 Harbor Row<br>Marlow, FL 30412</div>
      </div>
      <div class="details__divider"></div>
      <div class="contact">
        <div class="contact__line">
          <svg class="contact__icon" viewBox="0 0 13 15" aria-hidden="true">
            <rect x="2.5" y="0.5" width="8" height="14" rx="1.5" fill="var(--accent-yellow)"/>
            <rect x="4" y="2.5" width="5" height="7" fill="var(--ink-black)"/>
            <circle cx="6.5" cy="12" r="1" fill="var(--ink-black)"/>
          </svg>
          <span>555-214-6630</span>
        </div>
        <div class="contact__line">
          <svg class="contact__icon" viewBox="0 0 13 15" aria-hidden="true">
            <path d="M1 6 Q6.5 2 12 6 L11 8 L9 7 L9 6 Q6.5 5 4 6 L4 7 L2 8 Z" fill="var(--accent-yellow)"/>
            <rect x="2" y="9" width="9" height="5" rx="1" fill="var(--accent-yellow)"/>
          </svg>
          <span>555-327-1184</span>
        </div>
      </div>
    </div>
  </section>

  <section class="card card--back" aria-label="Card back">
    <div class="back__brand">Tidal Lanes</div>
    <div class="back__web">www.tidallanes.com</div>
  </section>

</main>
</body>
</html>
```